Maple Grove Schools | brand new stationery!

We need stationery design with our new logo! Our company updated it's name and image and we like to incorporate the new one on our stationery, business cards and email signature. We are looking for fresh, new ideas!
Industry: Childcare, Elementary and Middle School
Company Name: Maple Grove Schools
Tagline: Bright Futures Start Here
Main colors: Blue, white and a little yellow
Star shape is something new for us! Do you see a way to incorporate it as a design element?

```html
<!DOCTYPE html>
<html lang="en">
<head>
<meta charset="UTF-8">
<title>Maple Grove Schools – Email Signature</title>
<link href="https://fonts.googleapis.com/css2?family=Raleway:wght@700&family=Roboto:wght@400&family=Poppins:wght@600&display=swap" rel="stylesheet">
<style>
  :root {
    --navy: #262a6b;
    --yellow: #f9b712;
    --text-grey: #6d6e71;
    --ink: #1f1f1f;
    --paper: #ffffff;
    --backdrop: #d1d2d4;
  }
  * { margin: 0; padding: 0; box-sizing: border-box; }
  html, body {
    width: 1200px;
    height: 1200px;
    overflow: hidden;
    background: var(--backdrop);
  }
  .signature {
    position: absolute;
    left: 158px;
    top: 472px;
    width: 887px;
    height: 260px;
    background: var(--paper);
    overflow: hidden;
  }
  .signature__wave {
    position: absolute;
    inset: 0;
    width: 100%;
    height: 100%;
  }
  .person {
    position: absolute;
    left: 58px;
    top: 102px;
    width: 260px;
  }
  .person__name {
    font-family: "Raleway", sans-serif;
    font-weight: 700;
    font-size: 24px;
    color: var(--navy);
    line-height: 30px;
    white-space: nowrap;
  }
  .person__role {
    font-family: "Roboto", sans-serif;
    font-size: 21px;
    color: var(--yellow);
    line-height: 28px;
  }
  .tagline {
    position: absolute;
    left: 58px;
    top: 224px;
    font-family: "Roboto", sans-serif;
    font-size: 13px;
    color: var(--paper);
  }
  .contact {
    position: absolute;
    left: 343px;
    top: 56px;
    list-style: none;
    font-family: "Roboto", sans-serif;
    font-size: 19px;
    color: var(--text-grey);
    line-height: 25px;
  }
  .contact__item {
    display: flex;
    align-items: flex-start;
    gap: 8px;
    margin-bottom: 4px;
    white-space: nowrap;
  }
  .contact__item--address { margin-bottom: 10px; }
  .contact__icon {
    flex: 0 0 20px;
    width: 20px;
    height: 20px;
    margin-top: 3px;
    fill: var(--yellow);
  }
  .brand {
    position: absolute;
    left: 618px;
    top: 56px;
    width: 220px;
    text-align: center;
    font-family: "Poppins", sans-serif;
    font-weight: 600;
    color: var(--ink);
  }
  .brand__dot {
    display: block;
    width: 66px;
    height: 66px;
    margin: 0 auto 10px;
    border-radius: 50%;
    background: var(--navy);
  }
  .brand__name {
    font-size: 30px;
    line-height: 34px;
  }
</style>
</head>
<body>
  <section class="signature">
    <svg class="signature__wave" viewBox="0 0 887 260" preserveAspectRatio="none" aria-hidden="true">
      <path d="M130,196 C400,228 650,232 887,210" fill="none" stroke="var(--yellow)" stroke-width="4"/>
      <path d="M0,180 C300,222 600,236 887,220 L887,260 L0,260 Z" fill="var(--navy)"/>
    </svg>

    <div class="person">
      <p class="person__name">DAVID K. WHITMAN</p>
      <p class="person__role">Founder &amp; CEO</p>
    </div>

    <p class="tagline">Bright Futures Start Here</p>

    <ul class="contact">
      <li class="contact__item contact__item--address">
        <svg class="contact__icon" viewBox="0 0 24 24"><path d="M12 2a7 7 0 0 0-7 7c0 5 7 13 7 13s7-8 7-13a7 7 0 0 0-7-7zm0 9.5A2.5 2.5 0 1 1 12 6.5a2.5 2.5 0 0 1 0 5z"/></svg>
        <span>480 Birch Lane, Suite<br>3 Fairview, MA 01920</span>
      </li>
      <li class="contact__item">
        <svg class="contact__icon" viewBox="0 0 24 24"><path d="M6.6 10.8a15 15 0 0 0 6.6 6.6l2.2-2.2a1 1 0 0 1 1-.25 11.4 11.4 0 0 0 3.6.6 1 1 0 0 1 1 1V20a1 1 0 0 1-1 1A17 17 0 0 1 3 4a1 1 0 0 1 1-1h3.5a1 1 0 0 1 1 1c0 1.25.2 2.45.6 3.6a1 1 0 0 1-.25 1z"/></svg>
        <span>(555) 318-4026</span>
      </li>
      <li class="contact__item">
        <svg class="contact__icon" viewBox="0 0 24 24"><path d="M2 5h20v14H2zm2 2v.5l8 5 8-5V7zm0 2.8V17h16V9.8l-8 5z"/></svg>
        <span>info@maplegrove.org</span>
      </li>
      <li class="contact__item">
        <svg class="contact__icon" viewBox="0 0 24 24"><path d="M12 2a10 10 0 1 0 0 20 10 10 0 0 0 0-20zm6.9 9h-3a15 15 0 0 0-1.3-5.6A8 8 0 0 1 18.9 11zM12 4.1c.9 1.2 1.8 3.6 1.9 6.9h-3.8c.1-3.3 1-5.7 1.9-6.9zM9.4 5.4A15 15 0 0 0 8.1 11h-3a8 8 0 0 1 4.3-5.6zM5.1 13h3a15 15 0 0 0 1.3 5.6A8 8 0 0 1 5.1 13zm6.9 6.9c-.9-1.2-1.8-3.6-1.9-6.9h3.8c-.1 3.3-1 5.7-1.9 6.9zm2.6-1.3a15 15 0 0 0 1.3-5.6h3a8 8 0 0 1-4.3 5.6z"/></svg>
        <span>www.maplegrove.org</span>
      </li>
    </ul>

    <div class="brand">
      <span class="brand__dot" aria-hidden="true"></span>
      <p class="brand__name">Maple Grove<br>Schools</p>
    </div>
  </section>
</body>
</html>
```